Web Design Project

i'm looking for a sleek modern design i can use for a web site that deals with.
Intelligent Data Capture
Accounts Payable Solutions for faster processing based on our scanning solution.
ultimately we are a intelligent scanning software.

here is a great website, that does exactly what we do, and we like to have most of their services and products.

so something in this idea would be great.
www.valtrino.com

so i guess i want a good landing/home page which is smartly designed so users will be inclined to leave their information.

and then information pages.

also i dont need any cms for you to include, i only need you to hook the html hooks for RANK Kettle as i already have a CMS and need it to hook in to that, i am including links to that cheat sheet.
so it is easier when included as you create the Theme.

http://www.rankkettle.com/how-to-create-website-template.html
http://www.rankkettle.com/cheat-sheet.html
Updates

Hi Guys sorry for the long pause in design, but here is where we stand.

what ever design i choose, i need that designer to customize a few things for me based on design that was designed.
and i will need designer to match that them to work with RANK Kettle
here is the cheat sheet for the hooks that we need to match and make it work.
if you have any questions let me know.

otherwise i look forward to working with you. and good luck.

Target Market(s)

CFO's AP Managers, mostly ppl who are not Tech freindly

Industry/Entity Type

Software

Requirements
Must have
• i need on home page, the rotating banner should have 1 ability to place youtube links to show videos, and also ability to add buttons on these rotating banners that will allow forms to pop up take to another page.

```html
<!DOCTYPE html>
<html lang="en">
<head>
<meta charset="utf-8">
<title>Vorn – Document Imaging and Digital Conversion</title>
<link href="https://fonts.googleapis.com/css2?family=Ubuntu:wght@400;500;700&display=swap" rel="stylesheet">
<style>
:root{
  --red:#cc0a0a;
  --red-dark:#a80606;
  --ink:#222;
  --text:#555;
  --grey-bg:#6d7683;
  --light-bg:#f1f1f1;
  --footer:#5a5a5a;
  --white:#fff;
  --border:#d4d4d4;
}
*{box-sizing:border-box;margin:0;padding:0}
html,body{width:1029px;height:1200px;overflow:hidden}
body{font-family:"Ubuntu",sans-serif;position:relative;background:var(--light-bg);color:var(--text)}
.abs{position:absolute}

/* header */
.site-header{left:0;top:0;width:1029px;height:79px;background:linear-gradient(#fff,#e9e9e9)}
.brand{left:111px;top:24px;display:flex;align-items:center;gap:9px;font-size:30px;font-weight:400;color:#555}
.brand-mark{width:12px;height:12px;background:var(--red)}
.search{left:635px;top:8px;width:137px;height:18px;border:1px solid #bbb;border-radius:3px;background:#fff}
.search svg{position:absolute;right:3px;top:1px}
.lang{left:782px;top:10px;width:20px;height:12px;background:#2a3d8f;border:1px solid #999}
.lang-caret{left:806px;top:14px;width:0;height:0;border-left:5px solid transparent;border-right:5px solid transparent;border-top:5px solid var(--red)}
.utility{left:836px;top:11px;font-size:10px;color:#666}
.call{left:742px;top:42px;font-size:13px;color:var(--red)}
.call b{font-weight:400;font-size:19px;color:#333;letter-spacing:.5px}

/* nav */
.main-nav{left:0;top:79px;width:1029px;height:43px;background:linear-gradient(var(--red),var(--red-dark));border-top:1px solid #e44}
.main-nav ul{list-style:none;position:absolute;left:111px;top:0;width:807px;height:43px;display:flex;justify-content:space-between;align-items:center}
.main-nav li{color:#fff;font-size:13px}

/* grey band */
.grey-band{left:0;top:122px;width:1029px;height:628px;background:var(--grey-bg)}

.hero{left:111px;top:133px;width:807px;height:340px;border:2px solid #fff;border-radius:3px;background:linear-gradient(100deg,#6fb3dc 0%,#3d8fc6 45%,#1b5d92 75%,#16324f 100%)}
.hero h1{position:absolute;left:27px;top:116px;font-size:33px;line-height:41px;font-weight:700;color:#111}
.hero-arrow{position:absolute;top:289px;width:34px;height:34px;border-radius:50%;background:linear-gradient(#fff,#ddd);box-shadow:0 1px 3px rgba(0,0,0,.4)}

.news{left:111px;top:486px;width:807px;height:56px;background:linear-gradient(#fff,#e4e4e4);border-radius:3px;display:flex;align-items:center;padding-left:15px}
.news h3{font-size:16px;font-weight:400;color:var(--red);margin-right:13px}
.news p{font-size:11px;color:#555}
.news p em{color:var(--red)}

.card{top:555px;width:258px;height:178px;background:linear-gradient(#fff,#ececec);border-radius:3px;padding:14px 13px}
.card h2{font-size:20px;font-weight:400;color:#222;margin-bottom:3px}
.card p{font-size:11.2px;line-height:19.7px;color:#555;padding-left:2px;padding-right:6px}
.card .more{position:absolute;right:14px;bottom:10px;font-size:11px;color:var(--red)}

/* welcome */
.welcome{left:112px;top:770px;width:531px;height:169px;background:#fff;border:2px solid #ddd;border-radius:3px}
.ribbon{height:36px;background:var(--red);color:#fff;font-size:20px;padding:6px 23px}
.ribbon-fold{width:0;height:0;border-top:8px solid #6a0000;border-left:8px solid transparent}
.welcome p{position:absolute;left:13px;top:59px;width:505px;font-size:11.1px;line-height:17.2px}
.welcome .more{position:absolute;right:13px;bottom:10px;font-size:11px;color:var(--red)}

.how-title{left:660px;top:766px;font-size:20px;color:var(--red)}
.video{left:660px;top:793px;width:258px;height:148px;border:3px solid #fff;box-shadow:0 1px 4px rgba(0,0,0,.3);background:linear-gradient(135deg,#6a6f68,#4e5650 50%,#77806f)}

/* partners */
.partners{left:112px;top:959px;width:806px;height:115px;background:#fff;border:2px solid #ddd;border-radius:3px}
.partner-row{left:124px;top:1030px;width:784px;display:flex;justify-content:space-between;align-items:center;font-size:12px;font-weight:700;color:#444}

/* footer */
.site-footer{left:0;top:1087px;width:1029px;height:113px;background:var(--footer);color:#eee}
.foot-links{left:111px;top:1113px;font-size:10px;color:#fff;word-spacing:2px}
.copyright{left:111px;top:1164px;font-size:10px;color:#ddd}
.follow{left:744px;top:1113px;font-size:13px;font-weight:500;color:#fff}
.social{top:1139px;width:25px;height:25px;border-radius:3px}
</style>
</head>
<body>

<header class="abs site-header"></header>
<div class="abs brand"><span class="brand-mark"></span>Vorn</div>
<div class="abs search"><svg width="14" height="14" viewBox="0 0 14 14"><circle cx="5.5" cy="5.5" r="4" fill="none" stroke="#c00" stroke-width="1.8"/><line x1="8.5" y1="8.5" x2="13" y2="13" stroke="#c00" stroke-width="2.2"/></svg></div>
<div class="abs lang"></div>
<div class="abs lang-caret"></div>
<div class="abs utility">Find Us &nbsp;| &nbsp;Login</div>
<div class="abs call">Call Us: <b>012 555 0147</b></div>

<nav class="abs main-nav">
  <ul>
    <li><svg width="17" height="15" viewBox="0 0 17 15"><path d="M8.5 0 17 8h-2.5v7h-4v-5h-4v5h-4V8H0z" fill="#fff"/></svg></li>
    <li>About Us</li><li>Products</li><li>Solution</li><li>Supports</li><li>Partners</li><li>Events</li><li>Blog</li><li>Contact Us</li>
  </ul>
</nav>

<div class="abs grey-band"></div>

<section class="abs hero" role="img" aria-label="Banner photo: businessman pressing a glowing virtual keypad">
  <h1>Document Imaging and<br>Digital Conversion.</h1>
  <div class="hero-arrow" style="left:30px"><svg width="34" height="34" viewBox="0 0 34 34"><path d="M19 10l-7 7 7 7" fill="none" stroke="#333" stroke-width="3"/></svg></div>
  <div class="hero-arrow" style="left:77px"><svg width="34" height="34" viewBox="0 0 34 34"><path d="M15 10l7 7-7 7" fill="none" stroke="#333" stroke-width="3"/></svg></div>
</section>

<div class="abs news"><h3>Latest News:</h3><p>Lorem ipsum dolor sit amet consectetur adipiscing eiusmod tempor incididunt ut labore et dolore magna aliqua... <em>Read More</em></p></div>

<article class="abs card" style="left:111px"><h2>Case Studies</h2><p>Duis aute irure dolor in reprehenderit in voluptate velit esse cillum dolore euugiat nulla pariatur. Sed ut perspiciatis unde omnis iste natus error sit voluptatem accusantium dolorem- que laudantium.</p><span class="more">READ MORE&gt;&gt;</span></article>
<article class="abs card" style="left:386px"><h2>Free Trials</h2><p>Duis aute irure dolor in reprehenderit in voluptate velit esse cillum dolore euugiat nulla pariatur. Sed ut perspiciatis unde omnis iste natus error sit voluptatem accusantium dolorem- que laudantium.</p><span class="more">READ MORE&gt;&gt;</span></article>
<article class="abs card" style="left:660px"><h2>Webnairs</h2><p>Duis aute irure dolor in reprehenderit in voluptate velit esse cillum dolore euugiat nulla pariatur. Sed ut perspiciatis unde omnis iste natus error sit voluptatem accusantium dolorem- que laudantium.</p><span class="more">READ MORE&gt;&gt;</span></article>

<section class="abs welcome">
  <p>Lorem ipsum dolor sit amet, consectetur adipiscing elit. Fusce accumsan, elit a suscipit sagittis, tortor sapien cursus risus, non rhoncus lectus nunc ac nulla. Aliquam molestie, mi et imperdiet euismod, dui purus auctor tellus, et interdum lacus lectus et ante. Sed accumsan sollicitudin sapien, sit amet adipi-scing turpis gravida ac. In congue, neque ac lobortis volutpat, libero mauris varius mi, vitae suscipit ipsum ligula vitae risus.</p>
  <span class="more">READ MORE&gt;&gt;</span>
</section>
<div class="abs ribbon" style="left:103px;top:783px;width:237px">Welcome to Our Site</div>
<div class="abs ribbon-fold" style="left:103px;top:819px"></div>

<h2 class="abs how-title" style="font-weight:400">How it Works</h2>
<div class="abs video" role="img" aria-label="Video still: data and information word cloud with chain">
  <svg style="position:absolute;left:98px;top:34px" width="54" height="54" viewBox="0 0 54 54"><circle cx="27" cy="27" r="26" fill="#eee" opacity=".9"/><path d="M21 15l19 12-19 12z" fill="#333"/></svg>
</div>

<section class="abs partners"></section>
<div class="abs ribbon" style="left:103px;top:970px;width:237px">Our Partners</div>
<div class="abs ribbon-fold" style="left:103px;top:1006px"></div>
<div class="abs partner-row">
  <span>Halvard Trust</span><span>Lumora</span><span>Brevix</span><span>Castell Aero</span><span>Fablewood Studios</span><span>Harbor Mutual</span><span>Medrin</span><span>Quellis</span>
</div>

<footer class="abs site-footer"></footer>
<div class="abs foot-links">Home &nbsp;/&nbsp; About Us &nbsp;/&nbsp; Products &nbsp;/&nbsp; Solution &nbsp;/&nbsp; Support &nbsp;/&nbsp; Partners &nbsp;/&nbsp; Events &nbsp;/&nbsp; Blog &nbsp;/&nbsp; Contact</div>
<div class="abs copyright">© 2013 by <span style="color:#fff">Vorn</span>. All Right Reserved &nbsp;| &nbsp;Privacy Policy</div>
<div class="abs follow">Follow us on :</div>
<div class="abs social" style="left:746px;background:#3b5a99"></div>
<div class="abs social" style="left:783px;background:#4fb8dd"></div>
<div class="abs social" style="left:820px;background:#c8241c"></div>
<div class="abs social" style="left:856px;background:#2a7fb5"></div>
<div class="abs social" style="left:893px;background:#ef8b1e"></div>

</body>
</html>
```